The Harbor Promise (Poster Design ) for TV Show

“The Harbor Promise” tells the inspirational stories of the men and women who founded and built incredible companies from nothing. The show is hosted by Oscar-nominated actor Dale Whitcombe.

Looking for a inspirational poster design for a TV show

Design i like
https://img.craftloom.example/48210377/r/il/b4e1d2/2947106615/il_1588xN.2947106615_qk7m.jpg

https://media.pitchvault.example/Rt518LkWzN4HD9mP2aE7yQbXvcA=/375x231:1749x1605/500x500/top/smart/pitchvault-attachments/208/208471/attachment_208471593

https://thumbs.seekmore.example/images?q=tbn:XbR4tw9Lmz2Kq8Vn3PaHcUeYd7_JF6gsBpWRt&usqp=CAU

https://files.pagecraft.example/content/v1/6a3c91f2b8475dd1e3ab9264/2847361950218-KTW8M3QNZPLH42F9XAD5/QWTRMPK.jpg

https://static.reelhaven.example/images/journal/post_images/47205/images-w1400.jpg?1739204681

https://img.chatterbox.example/7k2wpd9xhn384.jpg

https://i.moodpin.example/736x/3c/8d/b1/3c8db1f72a0954e1d6c83b905f24e17c--film-posters-poster-design.jpg

Segment of the show to get a better understanding
https://clipstream.example/582049163/b7e3c915a2

Font styles to use
Serif
Sans Serif
Script

Requirements
Must have
• The Harbor Promise

```html
<!DOCTYPE html>
<html lang="en">
<head>
<meta charset="utf-8">
<title>The Harbor Promise — Poster</title>
<link href="https://fonts.googleapis.com/css2?family=Arimo:wght@400;700&display=swap" rel="stylesheet">
<style>
  :root {
    --backdrop: #2b2b2b;
    --ink: #ffffff;
    --sky-navy: #1b2a4a;
    --sky-blue: #34466e;
    --flag-red: #7a2f36;
    --cloud-ember: #b8523a;
    --sunset-gold: #e3a23a;
    --ground-dark: #2a1c14;
  }
  * { margin: 0; padding: 0; box-sizing: border-box; }
  html, body {
    width: 1200px; height: 1200px; overflow: hidden;
    background: var(--backdrop);
    font-family: "Arimo", Arial, sans-serif;
    color: var(--ink);
  }
  .poster {
    position: absolute; left: 200px; top: 36px;
    width: 800px; height: 1129px;
    overflow: hidden;
    box-shadow: 4px 6px 14px rgba(0,0,0,0.6);
  }
  .poster__scene {
    position: absolute; inset: 0;
    background:
      radial-gradient(ellipse 60% 30% at 55% 92%, rgba(227,162,58,0.85), rgba(227,162,58,0) 70%),
      linear-gradient(160deg, rgba(27,42,74,0) 40%, rgba(122,47,54,0.45) 60%, rgba(27,42,74,0) 75%),
      linear-gradient(180deg,
        var(--sky-navy) 0%,
        var(--sky-blue) 35%,
        #4a5670 48%,
        var(--cloud-ember) 62%,
        #a8643f 78%,
        var(--sunset-gold) 88%,
        var(--ground-dark) 100%);
  }
  .poster__rule {
    position: absolute; width: 2px; background: var(--ink);
  }
  .poster__rule--title { left: 204px; top: 51px; height: 523px; }
  .poster__rule--host { left: 746px; top: 977px; height: 102px; }

  .title { position: absolute; inset: 0; font-weight: 700; line-height: 1; }
  .title__the {
    position: absolute; left: 50px; top: 102px;
    font-size: 74px; letter-spacing: 1px;
  }
  .title__main {
    position: absolute; right: 51px; top: 131px;
    font-size: 98px; text-align: right; line-height: 0.97;
    letter-spacing: -1px;
  }
  .title__main span { display: block; }

  .tagline {
    position: absolute; right: 51px; top: 330px; width: 540px;
    text-align: right; font-size: 24px; line-height: 32px; font-weight: 400;
  }

  .host {
    position: absolute; right: 62px; top: 986px;
    text-align: right; line-height: 1;
  }
  .host__lead { font-size: 15.5px; font-weight: 400; letter-spacing: 0.2px; }
  .host__credit { font-size: 31px; font-weight: 700; margin-top: 7px; letter-spacing: -0.3px; }
  .host__name { font-size: 27px; margin-top: 6px; letter-spacing: -0.3px; }
  .host__name b { font-weight: 700; }
  .host__name span { font-weight: 400; }
</style>
</head>
<body>
  <main class="poster">
    <div class="poster__scene" role="img" aria-label="A waving flag blended with a sunset sky and clouds over a field, with a couple seen from behind holding hands"></div>

    <div class="poster__rule poster__rule--title"></div>

    <h1 class="title">
      <span class="title__the">THE</span>
      <span class="title__main"><span>HARBOR</span><span>PROMISE</span></span>
    </h1>

    <p class="tagline">tells the inspirational stories of the men and women who founded and built incredible companies from nothing.</p>

    <div class="host">
      <p class="host__lead">THE SHOW IS HOSTED BY</p>
      <p class="host__credit">OSCAR-NOMINATED</p>
      <p class="host__name"><span>ACTOR </span><b>DALE WHITCOMBE</b></p>
    </div>
    <div class="poster__rule poster__rule--host"></div>
  </main>
</body>
</html>
```